BorrowNest Website design, we are a home loan / lending company

We are a finance broking company that can do mortgages / home loans, Car Loans, Commercial Loans, SMSF Loans, Business Loans, Personal Loans
We are looking for a simple website, not too busy, easy to navigate, something that prompts customers to action or call us.
I like the simplicity of the following websites:
https://www.velkarafinance.com.au/ - I like this website front page. I was thinking I have my logo, the one with the black background appear , then the toolbar at the top perhaps?
https://trevix.com.au/business-loans# - on this page there are images under finance that works for you that I like that concept.
https://dunmerel.com.au/contact/ - I like the Make an Appointment page
https://trevix.com.au/about-us - Simple but effective page design

Target Market(s)

Home Loan Customer

Industry/Entity Type

Finance / Home Loans

Coding

Coded - Design and coding required

Number of Pages Required

5+ page

Font styles to use
Serif

Colors
0094D4
00A9DD
6FCCEA
C7EBF8
E9F6FB

Requirements
Must have
• The following Heading s - Contact Us, About Us, Our People, Make an Appointment, Loan Options, Calculators, Reviews. I want to use the Logo colours I have in the zip files I uploaded.
Nice to have
• Simple clean design

```html
<!DOCTYPE html>
<html lang="en">
<head>
<meta charset="utf-8">
<title>BorrowNest – Home Loans &amp; Lending</title>
<link href="https://fonts.googleapis.com/css2?family=Poppins:wght@300;400;500;600;700;800&display=swap" rel="stylesheet">
<style>
:root{
  --blue:#0094D4;
  --cyan:#00A9DD;
  --sky:#6FCCEA;
  --ice:#C7EBF8;
  --mist:#E9F6FB;
  --ink:#111418;
  --text:#4a4f55;
  --grey:#f2f3f5;
  --footer:#0c0c0e;
}
*{box-sizing:border-box;margin:0;padding:0}
html,body{width:1200px;height:4237px;overflow:hidden}
body{font-family:'Poppins',sans-serif;color:var(--ink);background:#fff;position:relative}
a{color:inherit;text-decoration:none}
.abs{position:absolute}

/* header */
.site-header{position:absolute;top:0;left:0;width:1200px;height:105px;background:#fff;z-index:3}
.brand{left:110px;top:12px;font-size:40px;font-weight:600;color:var(--ink);letter-spacing:-1px;display:flex;align-items:center;gap:10px}
.brand .mark{width:14px;height:14px;background:var(--cyan);border-radius:50%}
.top-contact{top:28px;font-size:15px;color:var(--blue);display:flex;align-items:center;gap:7px}
.top-sep{top:24px;width:1px;height:22px;background:#9aa}
.appt-btn{left:909px;top:18px;width:179px;height:40px;border:1.5px solid var(--blue);border-radius:6px;color:var(--blue);font-size:14px;display:flex;align-items:center;justify-content:center}
.main-nav{position:absolute;left:110px;top:72px;width:978px;height:64px;background:var(--blue);border-radius:8px 8px 0 0;z-index:4;color:#fff;font-size:15px}
.main-nav a{position:absolute;top:21px}
.main-nav a.active{font-weight:600;border-bottom:2px solid #fff;padding-bottom:1px}
.nav-search{position:absolute;left:932px;top:20px;width:26px;height:26px;background:#fff;border-radius:50%;display:flex;align-items:center;justify-content:center}

/* hero */
.hero{position:absolute;top:105px;left:0;width:1200px;height:599px;overflow:hidden}
.hero-photo{position:absolute;inset:0;background:linear-gradient(100deg,#f3ede6 0%,#efe7de 45%,#d9d3ce 65%,#b7c4cf 100%)}
.hero-strip{position:absolute;left:0;bottom:0;width:1200px;height:26px;background:var(--cyan);clip-path:polygon(0 80%,100% 0,100% 100%,0 100%)}
.hero-kicker{left:110px;top:178px;font-size:33px;font-weight:500}
.hero-title{left:110px;top:218px;font-size:56px;font-weight:600;color:var(--ink)}
.hero-text{left:110px;top:290px;width:370px;font-size:14px;line-height:26px;color:var(--text)}
.btn{background:var(--cyan);color:#fff;border-radius:6px;display:flex;align-items:center;justify-content:center;font-weight:500;box-shadow:0 6px 14px rgba(0,169,221,.35)}
.hero-btn{left:110px;top:384px;width:143px;height:55px;font-size:18px}

/* section heads */
.kicker{position:absolute;width:1200px;text-align:center;font-size:14px;font-weight:600;letter-spacing:6px;color:var(--cyan)}
.title{position:absolute;width:1200px;text-align:center;font-size:35px;font-weight:700}

/* loan options */
.options{position:absolute;top:704px;left:0;width:1200px;height:521px;background:#fff;overflow:hidden}
.options .swirl{right:10px;top:40px}
.options-sub{position:absolute;top:168px;width:1200px;text-align:center;font-size:16px;color:var(--text)}
.step{position:absolute;top:206px;width:230px;text-align:center}
.step svg{display:block;margin:0 auto}
.step h3{font-size:19px;font-weight:600;margin-top:16px}
.step p{font-size:13px;line-height:25px;color:var(--text);margin-top:8px}
.read-more{display:inline-flex;gap:8px;align-items:center;font-size:15px;font-weight:600;margin-top:10px}
.read-more span{border-bottom:1.5px solid var(--ink)}

/* about */
.about{position:absolute;top:1225px;left:0;width:1200px;height:595px;overflow:hidden}
.about-photo{position:absolute;inset:0;background:linear-gradient(90deg,#1a7fc6 0%,#2d9be0 40%,#2c9fe4 100%)}
.about-band{position:absolute;left:0;width:1200px;height:20px;background:var(--cyan)}
.about-circle{left:120px;top:95px;width:420px;height:420px;border-radius:50%;background:radial-gradient(circle at 55% 45%,#c8dceb 0%,#5ea9dc 55%,#2d86c9 100%);border:10px solid rgba(255,255,255,.9)}
.about-copy{left:600px;top:92px;width:500px;color:#fff}
.about-copy .k{font-size:14px;font-weight:600;letter-spacing:6px}
.about-copy h2{font-size:35px;font-weight:700;margin-top:6px}
.about-copy p{font-size:15px;line-height:29px;margin-top:14px}
.about-copy p + p{margin-top:30px}
.white-btn{left:603px;top:450px;width:141px;height:54px;background:#fff;color:var(--cyan);border-radius:6px;font-size:19px;font-weight:500;display:flex;align-items:center;justify-content:center}

/* services */
.services{position:absolute;top:1820px;left:0;width:1200px;height:575px;background:linear-gradient(120deg,#fbfbfc 0%,#eff0f2 50%,#fafafb 100%);overflow:hidden}
.service{position:absolute;top:177px;width:264px;text-align:center}
.service .pic{width:264px;height:264px;border-radius:50%;border:3px solid #fff;box-shadow:0 4px 14px rgba(0,0,0,.12)}
.service .label{font-size:21px;font-weight:500;margin-top:26px}
.service.featured .pic{position:relative;border:10px solid var(--cyan);background:linear-gradient(160deg,#6bc3ea,#1c9ad6);display:flex;flex-direction:column;align-items:center;justify-content:center;color:#fff;padding:0 40px}
.featured h3{font-size:20px;font-weight:600}
.featured p{font-size:13px;line-height:21px;margin-top:6px}
.featured a{font-size:13px;font-weight:600;text-decoration:underline;margin-top:4px}
.arrow-btn{width:28px;height:28px;border-radius:50%;background:#222;display:flex;align-items:center;justify-content:center}

/* contact */
.contact{position:absolute;top:2395px;left:0;width:1200px;height:750px;background:#fff}
.contact-band{position:absolute;top:0;left:0;width:1200px;height:474px;background:linear-gradient(90deg,#2a9be0 0%,#36a6e6 50%,#2a93d8 100%)}
.contact-band::before{content:"";position:absolute;top:0;left:0;width:1200px;height:12px;background:var(--cyan)}
.contact .kicker,.contact .title{color:#fff}
.contact-sub{position:absolute;top:155px;left:215px;width:770px;text-align:center;color:#fff;font-size:16px;line-height:26px}
.card{position:absolute;left:192px;top:237px;width:814px;height:429px;background:#fff;box-shadow:0 8px 30px rgba(0,0,0,.12)}
.card::after{content:"";position:absolute;left:35px;right:35px;bottom:0;height:3px;background:var(--cyan)}
.card-info{position:absolute;left:37px;top:85px;width:260px}
.card-info .small{font-size:14px;margin-top:12px}
.card-info h3{font-size:21px;font-weight:600;margin-top:2px}
.card-info p{font-size:12px;line-height:21px;color:var(--text);margin-top:8px}
.call{display:flex;align-items:center;gap:12px;margin-top:18px}
.call .ring{width:44px;height:44px;border-radius:50%;background:var(--cyan);display:flex;align-items:center;justify-content:center}
.call small{display:block;font-size:14px;color:var(--cyan)}
.call strong{font-size:21px;font-weight:600}
.field{position:absolute;background:#f4f5f6;font-size:12px;color:#555;padding:14px 15px}
.submit{left:357px;top:308px;width:141px;height:55px;font-size:19px;box-shadow:none}
.terms{position:absolute;left:520px;top:326px;font-size:13px;color:#555;display:flex;align-items:center;gap:10px}
.terms i{width:10px;height:10px;border-radius:50%;border:3px solid var(--ice);background:var(--cyan)}

/* testimonials */
.reviews{position:absolute;top:3145px;left:0;width:1200px;height:460px;background:var(--grey);overflow:hidden}
.quote-mark{left:110px;top:110px;font-size:150px;line-height:1;color:#bbb;font-weight:700}
.review-photo{left:112px;top:162px;width:205px;height:205px;border-radius:50%;border-bottom:8px solid var(--cyan);background:linear-gradient(180deg,#dfe4ea,#9aa6b3)}
.review-badge{left:272px;top:310px;width:48px;height:48px;border-radius:50%;background:#fff;border:4px solid var(--cyan)}
.review-body{left:368px;top:198px;width:716px}
.review-body h3{font-size:22px;font-weight:400}
.review-body h3 small{font-size:15px}
.review-body p{font-size:14px;line-height:28px;color:var(--text);margin-top:14px}

/* footer */
.site-footer{position:absolute;top:3584px;left:0;width:1200px;height:653px;background:var(--footer);color:#fff}
.footer-strip{position:absolute;top:-2px;left:0;width:1200px;height:32px;background:var(--cyan);clip-path:polygon(0 100%,0 55%,100% 0,100% 0,100% 15%,0 100%)}
.footer-h{font-size:20px;font-weight:500}
.socials{left:110px;top:148px;display:flex;gap:22px}
.socials span{width:36px;height:36px;border-radius:50%;border:1.5px solid var(--cyan)}
.newsletter{left:556px;top:148px;width:532px;height:46px;background:#fff;border-radius:4px;display:flex}
.newsletter span{flex:1;color:#222;font-size:12px;padding:15px 24px}
.newsletter b{width:154px;background:var(--cyan);border-radius:0 4px 4px 0;display:flex;align-items:center;justify-content:center;font-weight:500;font-size:17px}
.rule{left:110px;width:978px;height:1px;background:#555}
.links{top:300px}
.links h4{font-size:20px;font-weight:500;margin-bottom:14px}
.links li{list-style:none;font-size:15px;height:45px;display:flex;align-items:center;gap:18px}
.links li::before{content:"»";font-size:20px;font-weight:700;line-height:1}
.contact-list li::before{content:none}
.copyright{left:0;top:622px;width:1200px;text-align:center;font-size:13px}
</style>
</head>
<body>

<header class="site-header">
  <div class="abs brand"><span>BorrowNest</span></div>
  <div class="abs top-contact" style="left:470px">
    <svg width="14" height="14" viewBox="0 0 24 24"><path fill="#0094D4" d="M6.6 10.8a15 15 0 0 0 6.6 6.6l2.2-2.2c.3-.3.7-.4 1-.2 1.1.4 2.3.6 3.6.6.6 0 1 .4 1 1V20c0 .6-.4 1-1 1A17 17 0 0 1 3 4c0-.6.4-1 1-1h3.5c.6 0 1 .4 1 1 0 1.3.2 2.5.6 3.6.1.3 0 .7-.2 1z"/></svg>
    +1 555 010 2040
  </div>
  <div class="abs top-sep" style="left:639px"></div>
  <div class="abs top-contact" style="left:660px">
    <svg width="14" height="12" viewBox="0 0 24 18"><rect width="24" height="18" rx="2" fill="#0094D4"/><path d="M2 3l10 7 10-7" stroke="#fff" stroke-width="2" fill="none"/></svg>
    hello@borrownest.com
  </div>
  <div class="abs top-sep" style="left:884px"></div>
  <a class="abs appt-btn" href="#">Make An Appointment</a>
</header>

<nav class="main-nav">
  <a class="active" style="left:24px">Home</a>
  <a style="left:132px">About</a>
  <a style="left:238px">Our People</a>
  <a style="left:383px">Loan Options</a>
  <a style="left:545px">Calculators</a>
  <a style="left:695px">Reviews</a>
  <a style="left:818px">Contact Us</a>
  <span class="nav-search"><svg width="12" height="12" viewBox="0 0 24 24"><circle cx="10" cy="10" r="7" stroke="#0094D4" stroke-width="3" fill="none"/><path d="M15 15l6 6" stroke="#0094D4" stroke-width="3"/></svg></span>
</nav>

<section class="hero">
  <div class="hero-photo" role="img" aria-label="Smiling man in glasses reading a loan document at his desk"></div>
  <div class="abs hero-kicker">Welcome To</div>
  <h1 class="abs hero-title">BorrowNest</h1>
  <p class="abs hero-text">Itaque earum rerum hic tenetur a sapiente deletus, ut aut reiciendis voluptatibus maiores perferendis doloribus asperiores repellat.</p>
  <a class="abs btn hero-btn" href="#">Get Started</a>
  <div class="hero-strip"></div>
</section>

<section class="options">
  <div class="kicker" style="top:84px">PROCESS</div>
  <h2 class="title" style="top:110px">Loan Options</h2>
  <p class="options-sub">Itaque earum rerum hic tenetur a sapiente delectus, ut aut reiciendis voluptatibus maiores alias consequatur</p>

  <div class="step" style="left:102px">
    <svg width="72" height="72" viewBox="0 0 72 72" fill="none" stroke="#0094D4" stroke-width="2.5"><rect x="8" y="4" width="44" height="62" rx="3"/><circle cx="30" cy="22" r="7"/><path d="M18 42h24M18 50h20M18 58h14"/><path d="M60 28l6 6-18 18-7 1 1-7z"/></svg>
    <h3>Loan Application</h3>
    <p>Temporibus autem quibusdam et aut officiis debitis aut rerum necessita repudiandae.</p>
    <a class="read-more"><span>Read More</span>→</a>
  </div>
  <div class="step" style="left:358px">
    <svg width="72" height="72" viewBox="0 0 72 72" fill="none" stroke="#0094D4" stroke-width="2.5"><rect x="14" y="4" width="44" height="54" rx="3"/><path d="M22 18l3 3 5-6M34 18h16M22 30l3 3 5-6M34 30h16M22 42l3 3 5-6M34 42h16"/><path d="M6 52h60v14H6z"/></svg>
    <h3>Document Submission</h3>
    <p>At vero eos et accusamus et iusto odio dignissimos ducimus qui blanditiis praesentium.</p>
    <a class="read-more"><span>Read More</span>→</a>
  </div>
  <div class="step" style="left:613px">
    <svg width="80" height="72" viewBox="0 0 80 72" fill="none" stroke="#0094D4" stroke-width="2.5"><rect x="4" y="18" width="60" height="48" rx="3"/><circle cx="22" cy="38" r="6"/><path d="M12 58c2-7 18-7 20 0M38 36h18M38 44h18M38 52h12"/><circle cx="60" cy="16" r="12"/><path d="M54 16l4 4 8-8"/></svg>
    <h3>Verification</h3>
    <p>Similique sunt in culpa qui officia deserunt mollitia animi, laborum dolorum fuga.</p>
    <a class="read-more"><span>Read More</span>→</a>
  </div>
  <div class="step" style="left:866px">
    <svg width="72" height="72" viewBox="0 0 72 72" fill="none" stroke="#0094D4" stroke-width="2.5"><path d="M10 4h36l10 10v52H10z"/><path d="M18 20h22M18 28h22M18 36h14M18 44h14"/><circle cx="52" cy="42" r="12"/><path d="M52 35v14M48 39h6a2 2 0 0 1 0 4h-4a2 2 0 0 0 0 4h6"/><path d="M40 58h26v8H40z"/></svg>
    <h3>Loan Disbursal</h3>
    <p>Nam libero tempore, cumeram soluta nobis est eligendi optio cumque nihil impedit .</p>
    <a class="read-more"><span>Read More</span>→</a>
  </div>
</section>

<section class="about">
  <div class="about-photo" role="img" aria-label="Loan adviser smiling while reviewing paperwork with a client, washed in blue"></div>
  <div class="about-band" style="top:0"></div>
  <div class="about-band" style="bottom:0"></div>
  <div class="abs about-circle" role="img" aria-label="Close-up of a smiling adviser holding loan documents"></div>
  <div class="abs about-copy">
    <div class="k">ABOUT US</div>
    <h2>BorrowNest</h2>
    <p>Et harum quidem rerum facilis est et expedita distinctio. Nam libero tempore, cum soluta nobis est eligendi optio cumque nihil impedit quo minus id quod maxime placeat facere pimus, omnis voluptas dolor repellendus.</p>
    <p>Temporibus autem quibusdam et aut officiis debitis aut rerum necessitatibus saepe eveniet ut et voluptates repudiandae sinta sapiente delectus, ut aut reiciendis voluptatibus maiores alias et molestiae non recusandae.</p>
  </div>
  <a class="abs white-btn" href="#">Read More</a>
</section>

<section class="services">
  <div class="kicker" style="top:75px">SERVICES</div>
  <h2 class="title" style="top:102px">What We Offer</h2>
  <span class="abs arrow-btn" style="left:42px;top:314px"><svg width="14" height="14" viewBox="0 0 24 24"><path d="M20 12H5M11 5l-7 7 7 7" stroke="#fff" stroke-width="3" fill="none"/></svg></span>
  <div class="service" style="left:120px">
    <div class="pic" role="img" aria-label="Hand passing car keys across a desk" style="background:linear-gradient(150deg,#e7e2dc,#b9b2ab)"></div>
    <div class="label">Car Loans</div>
  </div>
  <div class="service featured" style="left:472px">
    <div class="pic" role="img" aria-label="Business team meeting behind a blue overlay">
      <h3>Commercial Loans</h3>
      <p>Itaque earum rerum hic tenetur a sapiente delectus, maiores.</p>
      <a href="#">Read More</a>
    </div>
  </div>
  <div class="service" style="left:822px">
    <div class="pic" role="img" aria-label="Woman smiling at her phone beside a laptop" style="background:linear-gradient(150deg,#c9ccd2,#6f7887)"></div>
    <div class="label">Business Loans</div>
  </div>
  <span class="abs arrow-btn" style="left:1135px;top:314px"><svg width="14" height="14" viewBox="0 0 24 24"><path d="M4 12h15M13 5l7 7-7 7" stroke="#fff" stroke-width="3" fill="none"/></svg></span>
</section>

<section class="contact">
  <div class="contact-band" role="img" aria-label="Office team at work under a blue overlay"></div>
  <div class="kicker" style="top:82px;color:#fff">CONTACT US</div>
  <h2 class="title" style="top:106px;color:#fff">Get In Touch With Us</h2>
  <p class="contact-sub">Nam libero tempore, cum soluta nobis est eligendi optio cumque nihil impedit quo minus id quod maxime placeat facere possimus.</p>
  <div class="card">
    <div class="card-info">
      <svg width="30" height="30" viewBox="0 0 30 30" fill="none" stroke="#00A9DD" stroke-width="1.6"><path d="M3 12l12-9 12 9v15H3z"/><path d="M3 12l12 9 12-9"/><circle cx="15" cy="11" r="3"/></svg>
      <div class="small">Get In Touch</div>
      <h3>Request a Quote</h3>
      <p>Itaque earum rerum hic tenetur a sapiente delectus, ut aut reiciendis voluptatibus maiores alias consequatur aut perferendis doloribus asperiores repellat.</p>
      <div class="call">
        <span class="ring"><svg width="22" height="22" viewBox="0 0 24 24"><path fill="#fff" d="M6.6 10.8a15 15 0 0 0 6.6 6.6l2.2-2.2c.3-.3.7-.4 1-.2 1.1.4 2.3.6 3.6.6.6 0 1 .4 1 1V20c0 .6-.4 1-1 1A17 17 0 0 1 3 4c0-.6.4-1 1-1h3.5c.6 0 1 .4 1 1 0 1.3.2 2.5.6 3.6.1.3 0 .7-.2 1z"/></svg></span>
        <div><small>Call Us Today!</small><strong>+1 555 010 2040</strong></div>
      </div>
    </div>
    <div class="field" style="left:357px;top:57px;width:197px;height:46px">First Name</div>
    <div class="field" style="left:580px;top:57px;width:197px;height:46px">Last Name</div>
    <div class="field" style="left:357px;top:117px;width:197px;height:46px">Email</div>
    <div class="field" style="left:580px;top:117px;width:197px;height:46px">Phone Number</div>
    <div class="field" style="left:357px;top:177px;width:420px;height:106px">Message</div>
    <a class="abs btn submit" href="#">Submit</a>
    <div class="terms"><i></i>I Accept the privacy &amp; terms</div>
  </div>
</section>

<section class="reviews">
  <div class="kicker" style="top:80px">TESTIMONIALS</div>
  <h2 class="title" style="top:106px">What Customer Says</h2>
  <span class="abs arrow-btn" style="left:42px;top:263px"><svg width="14" height="14" viewBox="0 0 24 24"><path d="M20 12H5M11 5l-7 7 7 7" stroke="#fff" stroke-width="3" fill="none"/></svg></span>
  <div class="abs quote-mark">“</div>
  <div class="abs review-photo" role="img" aria-label="Portrait of a smiling customer in a denim jacket"></div>
  <div class="abs review-badge"></div>
  <div class="abs review-body">
    <h3>Clara Venholt (<small>Senior Co-director</small>)</h3>
    <p>“Et harum quidem rerum facilis est et expedita distinctio. Nam libero tempore, cum placeat facere possimus, omnis voluptas assumenda est, omnis dolor repellendus. Temporibus autem quibusdam et aut officiis debitis aut rerum necessitatibus saepe eveniet ut et soluta nobis est eligendi optio cumque nihil impedit quo voluptates repudiandae sint et molestiae non recusandae. ”</p>
  </div>
  <span class="abs arrow-btn" style="left:1135px;top:263px"><svg width="14" height="14" viewBox="0 0 24 24"><path d="M4 12h15M13 5l7 7-7 7" stroke="#fff" stroke-width="3" fill="none"/></svg></span>
</section>

<footer class="site-footer">
  <div class="footer-strip"></div>
  <div class="abs footer-h" style="left:110px;top:102px">FOLLOW US ON</div>
  <div class="abs socials"><span></span><span></span><span></span><span></span></div>
  <div class="abs footer-h" style="left:556px;top:96px">SIGNUP FOR NEWSLETTER</div>
  <div class="abs newsletter"><span>Enter The Email</span><b>Subscribe</b></div>
  <div class="abs rule" style="top:256px"></div>

  <div class="abs links" style="left:110px"><h4>QUICK LINKS</h4><ul><li>Home</li><li>About us</li><li>Services</li><li>Contact Us</li></ul></div>
  <div class="abs links" style="left:359px"><h4>SERVICES</h4><ul><li>Car Loans</li><li>Home Loans</li><li>SMSF Loans</li><li>Business Loans</li></ul></div>
  <div class="abs links" style="left:610px"><h4>HELP LINKS</h4><ul><li>Support Links</li><li>Privacy Policy</li><li>Terms &amp; Conditions</li><li>Return Policy</li></ul></div>
  <div class="abs links contact-list" style="left:872px"><h4>CONTACT US</h4>
    <ul>
      <li style="align-items:flex-start;height:56px"><svg width="14" height="18" viewBox="0 0 14 18"><path fill="#fff" d="M7 0a7 7 0 0 0-7 7c0 5 7 11 7 11s7-6 7-11a7 7 0 0 0-7-7zm0 9.5A2.5 2.5 0 1 1 7 4.5a2.5 2.5 0 0 1 0 5z"/></svg><span style="line-height:22px">BorrowNest<br>United States</span></li>
      <li><svg width="16" height="16" viewBox="0 0 24 24"><path fill="#fff" d="M6.6 10.8a15 15 0 0 0 6.6 6.6l2.2-2.2c.3-.3.7-.4 1-.2 1.1.4 2.3.6 3.6.6.6 0 1 .4 1 1V20c0 .6-.4 1-1 1A17 17 0 0 1 3 4c0-.6.4-1 1-1h3.5c.6 0 1 .4 1 1 0 1.3.2 2.5.6 3.6.1.3 0 .7-.2 1z"/></svg>+1 555 010 2040</li>
      <li><svg width="16" height="12" viewBox="0 0 24 18"><rect width="24" height="18" rx="2" fill="#fff"/><path d="M2 3l10 7 10-7" stroke="#0c0c0e" stroke-width="2" fill="none"/></svg>hello@borrownest.com</li>
    </ul>
  </div>

  <div class="abs rule" style="top:564px"></div>
  <div class="abs copyright">Copyrights@2022.BorrowNest.All Rights Reserved</div>
</footer>

</body>
</html>
```